We need our current web site completely overhauled logo and all. www.maplecrestkidsclub.com

This is a web site for a before and after school program for kids. I would like to see a fresh and cleaner version. The current version was created 8 to 10 years ago.
www.maplecrestkidsclub.com

```html
<!DOCTYPE html>
<html lang="en">
<head>
<meta charset="utf-8">
<title>Maplecrest Kids Club</title>
<link href="https://fonts.googleapis.com/css2?family=Delius&family=Roboto:wght@400;500;700&display=swap" rel="stylesheet">
<style>
:root{
  --sky-top:#9fdcf7;
  --sky-mid:#c9ecfb;
  --sky-low:#eaf7fd;
  --green:#8fc21b;
  --orange:#ffa313;
  --red:#d8343d;
  --blue:#1fb3dc;
  --dark-green:#0f5a2c;
  --text:#3a3a3a;
  --muted:#555;
  --panel-border:#dcdcdc;
  --footer:#4a4a4a;
  --footer-text:#b9b9b9;
}
*{box-sizing:border-box;margin:0;padding:0}
html,body{width:1077px;height:1200px;overflow:hidden}
body{background:var(--sky-low);font-family:'Roboto',sans-serif}
.page{
  width:1200px;height:1337px;position:relative;
  transform:scale(0.8975);transform-origin:0 0;
  background:linear-gradient(180deg,var(--sky-top) 0,var(--sky-mid) 420px,var(--sky-low) 760px,#f4fbfe 1236px);
}
.brand{position:absolute;left:0;right:0;top:22px;text-align:center;display:flex;justify-content:center;align-items:center;gap:12px}
.brand-mark{width:38px;height:38px;border-radius:50%;background:var(--dark-green)}
.brand-name{font-family:'Delius',cursive;font-size:40px;color:#1d1d1d;line-height:1}
.nav{position:absolute;left:0;right:0;top:126px;display:flex;flex-direction:column;align-items:center;gap:9px}
.nav-row{display:flex;gap:9px}
.nav a{
  display:block;height:42px;line-height:40px;text-align:center;
  font-family:'Delius',cursive;font-size:19px;color:#fff;text-decoration:none;
  border:2px solid #fff;border-radius:4px;box-shadow:0 1px 3px rgba(0,0,0,.15);
}
.nav .g{background:var(--green)} .nav .o{background:var(--orange)}
.nav .r{background:var(--red)} .nav .b{background:var(--blue)}
.slider{position:absolute;left:129px;top:232px;width:942px;height:480px}
.slider svg{display:block}
.slide-arrow{position:absolute;top:153px;width:57px;height:80px;background:rgba(40,40,40,.75);display:flex;align-items:center;justify-content:center}
.slide-arrow.prev{left:6px}.slide-arrow.next{right:6px}
.features{position:absolute;left:130px;top:751px;display:flex;gap:20px}
.feature{width:300px;height:100px;border-radius:2px;display:flex;align-items:center;color:#fff;font-family:'Delius',cursive;font-size:35px;line-height:1}
.feature.health{background:linear-gradient(180deg,#3ac4f4,#15a3e4)}
.feature.tuition{background:linear-gradient(180deg,#7ccb1a,#5ba414)}
.feature.kids{background:linear-gradient(180deg,#f5556a,#e62c45)}
.feature .art{width:120px;height:92px;margin:0 28px 0 12px;border-radius:8px}
.health .art{background:rgba(255,255,255,.35)}
.tuition .art{background:rgba(255,230,150,.45)}
.kids .art{background:rgba(255,210,120,.45)}
.panel{position:absolute;top:870px;height:246px;background:#fff;border:1px solid var(--panel-border);border-radius:3px;padding:18px 18px 0}
.panel.welcome{left:129px;width:461px}
.panel.programs{left:609px;width:461px;padding-left:16px}
.panel h2{font-family:'Delius',cursive;font-weight:400;font-size:25px;color:#333;margin-bottom:10px}
.panel h2 span{color:var(--dark-green)}
.welcome p{font-size:13px;line-height:23px;color:var(--muted)}
.program-body{display:flex;gap:18px}
.program-poster{width:134px;height:140px;flex:none;background:linear-gradient(180deg,#8fe17a,#5cb85c 55%,#3f9ad0);margin-top:4px}
.program-list{list-style:none;font-size:13px;color:var(--muted)}
.program-list li{height:28px;display:flex;align-items:center;gap:8px;white-space:nowrap}
.read-more{display:inline-block;margin-top:8px;background:#555;color:#fff;font-size:13px;padding:6px 14px;border-radius:3px}
.newsletter{position:absolute;left:129px;top:1135px;width:942px;height:82px;border-radius:3px;background:linear-gradient(180deg,#ffa11c,#ff7e00);display:flex;align-items:center;padding-left:40px}
.newsletter h3{font-family:'Delius',cursive;font-weight:400;font-size:25px;color:#fff;width:264px}
.newsletter .email{width:470px;height:42px;background:#fff;border:1px solid #ddd;border-radius:3px;font-family:'Delius',cursive;font-size:16px;color:#999;line-height:40px;padding-left:14px}
.newsletter .signup{margin-left:18px;width:96px;height:44px;background:var(--dark-green);color:#fff;border-radius:3px;font-family:'Delius',cursive;font-size:16px;display:flex;align-items:center;justify-content:center}
.footer{position:absolute;left:0;top:1236px;width:1200px;height:101px;background:var(--footer)}
.copy{position:absolute;left:132px;top:28px;font-family:'Delius',cursive;font-size:14px;line-height:23px;color:var(--footer-text)}
.copy span{color:#fff}
.follow{position:absolute;right:130px;top:34px;display:flex;align-items:center;gap:7px;font-family:'Delius',cursive;font-size:14px;color:#fff}
.follow .label{margin-right:8px}
.social{width:32px;height:32px;border-radius:50%}
.social.s1{background:#3b5a98}.social.s2{background:#3fa9d6}.social.s3{background:#c9402c}
</style>
</head>
<body>
<div class="page">
  <header class="brand">
    <div class="brand-mark"></div>
    <div class="brand-name">Maplecrest Kids Club</div>
  </header>

  <nav class="nav">
    <div class="nav-row">
      <a class="g" style="width:84px">Home</a>
      <a class="o" style="width:103px">Programs</a>
      <a class="r" style="width:174px">The Maplecrest</a>
      <a class="b" style="width:173px">Party &amp; Rentals</a>
      <a class="g" style="width:114px">Kids Place</a>
      <a class="o" style="width:90px">Events</a>
      <a class="r" style="width:139px">Montessori</a>
    </div>
    <div class="nav-row">
      <a class="b" style="width:114px">About Us</a>
      <a class="g" style="width:174px">Tution Express</a>
      <a class="o" style="width:114px">Locations</a>
      <a class="r" style="width:114px">Careers</a>
      <a class="b" style="width:119px">Contact Us</a>
    </div>
  </nav>

  <section class="slider">
    <svg width="942" height="480" viewBox="0 0 942 480">
      <defs>
        <linearGradient id="photoTone" x1="0" y1="0" x2="0" y2="1">
          <stop offset="0" stop-color="#cfe6f3"/>
          <stop offset="0.38" stop-color="#e9ecd9"/>
          <stop offset="0.6" stop-color="#8fb45a"/>
          <stop offset="1" stop-color="#5e8e34"/>
        </linearGradient>
        <radialGradient id="shadow" cx="0.5" cy="0.5" r="0.5">
          <stop offset="0" stop-color="rgba(0,0,0,.18)"/>
          <stop offset="1" stop-color="rgba(0,0,0,0)"/>
        </radialGradient>
      </defs>
      <ellipse cx="471" cy="470" rx="400" ry="12" fill="url(#shadow)"/>
      <path d="M4 4 H938 V385 Q938 405 900 412 Q471 480 42 412 Q4 405 4 385 Z" fill="#fff" stroke="#d5d5d5" stroke-width="1.5"/>
      <path role="img" aria-label="Photo of smiling children playing with hula hoops on a sunny lawn" d="M6 6 H936 V382 Q936 398 900 404 Q471 470 42 404 Q6 398 6 382 Z" fill="url(#photoTone)"/>
    </svg>
    <div class="slide-arrow prev"><svg width="14" height="24" viewBox="0 0 14 24"><path d="M12 2 L2 12 L12 22" fill="none" stroke="#fff" stroke-width="2"/></svg></div>
    <div class="slide-arrow next"><svg width="14" height="24" viewBox="0 0 14 24"><path d="M2 2 L12 12 L2 22" fill="none" stroke="#fff" stroke-width="2"/></svg></div>
  </section>

  <section class="features">
    <div class="feature health"><div class="art" role="img" aria-label="Illustration of a medical team with a first aid kit"></div><div>Health<br>Tips</div></div>
    <div class="feature tuition"><div class="art" role="img" aria-label="Illustration of children gathered around a computer"></div><div>Tuition<br>Express</div></div>
    <div class="feature kids"><div class="art" role="img" aria-label="Illustration of happy children with balloons"></div><div>Kid's<br>Place</div></div>
  </section>

  <section class="panel welcome">
    <h2>Welcome to <span>Maplecrest Kids Club</span></h2>
    <p>The Maplecrest Before and After School Program exists to provide programming of the highest quality for your children, stressing a safe, secure environment; a nurturing, professional staff and lots of fun. We are committed to providing a fun-filled, rewarding program that supports the physical, mental, emotional and spiritual development of school-age children and their families to the fullest potential in order to improve their quality of life.</p>
  </section>

  <section class="panel programs">
    <h2>Our <span>Programs</span></h2>
    <div class="program-body">
      <div class="program-poster" role="img" aria-label="Summer camp flyer with group photos of campers"></div>
      <div>
        <ul class="program-list">
          <li><svg width="12" height="10" viewBox="0 0 12 10"><path d="M1 5 L4.5 8.5 L11 1" fill="none" stroke="var(--dark-green)" stroke-width="2.2"/></svg>Maplecrest Before &amp; After School Program</li>
          <li><svg width="12" height="10" viewBox="0 0 12 10"><path d="M1 5 L4.5 8.5 L11 1" fill="none" stroke="var(--dark-green)" stroke-width="2.2"/></svg>Maplecrest Summer Camp</li>
          <li><svg width="12" height="10" viewBox="0 0 12 10"><path d="M1 5 L4.5 8.5 L11 1" fill="none" stroke="var(--dark-green)" stroke-width="2.2"/></svg>Maplecrest Montessori School</li>
          <li><svg width="12" height="10" viewBox="0 0 12 10"><path d="M1 5 L4.5 8.5 L11 1" fill="none" stroke="var(--dark-green)" stroke-width="2.2"/></svg>Little Hoopers Basketball</li>
          <li><svg width="12" height="10" viewBox="0 0 12 10"><path d="M1 5 L4.5 8.5 L11 1" fill="none" stroke="var(--dark-green)" stroke-width="2.2"/></svg>Birthday Parties &amp; Gym Rentals</li>
        </ul>
        <span class="read-more">Read More</span>
      </div>
    </div>
  </section>

  <section class="newsletter">
    <h3>Newsletter Subscribe</h3>
    <div class="email">enter email address</div>
    <div class="signup">SIGN UP</div>
  </section>

  <footer class="footer">
    <div class="copy">Copyright ©2013. <span>Maplecrest Kids Club.</span><br>All Right Reserved</div>
    <div class="follow">
      <span class="label">Follow Us On:</span>
      <span class="social s1"></span><span class="social s2"></span><span class="social s3"></span>
    </div>
  </footer>
</div>
</body>
</html>
```